Creation of brand identity and website "Tandem K"

I am currently seeking an brand, identity and web design for a new project called Tandem K. This is a brand new concept from scratch and you have free-reign on the whole design process, taking into account my preference below.

Must include the name "Tandem K", or "Tandem K: Or the year I woke Up". Kudos is this forms part of the brands logo

Design that can be easily scaled to potentially include: a blog, timeline and vlogs.

Minimal but effective use of colour (however any colours and combinations permitted

Use of icons/graphics over text wherever possible

Minimal use of frames and borders

I appreciate this is a fairly wide scope so please contact me on marblefinch@postwillow.com with any questions or more information on what the project is.

Target Market(s)

Male and Female 20-40
Blog readers
Selfhelp

Industry/Entity Type

Seeking

Number of Pages Required

1 page

Font styles to use
Serif
Sans Serif

Requirements
Must have
• It is in effect a blog design, so about me section, recent blog / archived posts, reader comments / Q and A section.
• A coded design would be appreciated to make my life easier however I have left the design as uncoded as getting the right design matters more to me and I want to keep the project open to as many designers as possible
Nice to have
• See project description for other details and please ask if you need anything else :)
Should not have
• Mustn't be cluttered or feel fussy
• Promote icons over text
• Frames / multiple borders

```html
<!DOCTYPE html>
<html lang="en">
<head>
<meta charset="utf-8">
<title>Tandem K: Or the Year I Woke Up</title>
<link href="https://fonts.googleapis.com/css2?family=Cinzel:wght@400;600&family=Lato:wght@400;700&family=Questrial&family=PT+Sans+Narrow:wght@700&display=swap" rel="stylesheet">
<style>
:root{
  --orange:#f7a11a;
  --orange-deep:#e8900c;
  --ink:#222222;
  --text:#666666;
  --muted:#8a8a8a;
  --dark:#2c2c2c;
  --panel-head:#575b5d;
  --line:#e3e3e3;
  --soft:#f3f3f3;
  --white:#ffffff;
}
*{margin:0;padding:0;box-sizing:border-box}
html,body{width:1200px;height:3114px;overflow:hidden;background:var(--white)}
body{position:relative;font-family:"Lato",Arial,sans-serif;color:var(--text)}
.abs{position:absolute}

.topbar{left:0;top:0;width:1200px;height:46px;background:var(--orange)}
.topbar .dots{position:absolute;right:24px;top:13px;display:flex;gap:10px}
.topbar .dots span{width:20px;height:20px;border-radius:50%;background:var(--white)}

.brand{left:0;top:68px;width:1200px;text-align:center;font-family:"Cinzel",Georgia,serif;font-size:30px;font-weight:600;color:var(--ink);letter-spacing:1px}
.nav{left:0;top:126px;width:1200px;display:flex;justify-content:center;font-family:"Cinzel",Georgia,serif;font-size:17px;letter-spacing:2px;color:var(--ink)}
.nav a{color:inherit;text-decoration:none;padding:0 26px;border-left:1px solid #999;line-height:18px;position:relative}
.nav a:first-child{border-left:none;color:var(--orange)}
.nav a:first-child::after{content:"";position:absolute;left:26px;right:26px;bottom:-14px;height:3px;background:var(--orange)}

.hero{left:0;top:166px;width:1200px;height:401px;background:linear-gradient(180deg,#3b3a3a 0%,#7a5a2c 28%,#d98b22 48%,#9a5a18 62%,#2a2420 80%,#151515 100%)}
.hero .arrow{position:absolute;top:196px;width:22px;height:28px;background:rgba(120,120,120,.75)}
.hero .arrow svg{display:block;margin:8px auto}
.hero .tagline{position:absolute;left:0;top:276px;width:1200px;text-align:center;font-family:"PT Sans Narrow",Arial,sans-serif;font-weight:700;font-size:35px;line-height:42px;color:var(--white);text-shadow:0 1px 3px rgba(0,0,0,.5)}

.features{left:0;top:567px;width:1200px;height:153px;display:flex}
.feature{flex:1;display:flex;align-items:center;justify-content:center;gap:26px;background:var(--orange);font-family:"Cinzel",Georgia,serif;font-size:24px;letter-spacing:1.5px;color:var(--white)}
.feature.dark{background:var(--dark);color:var(--orange)}
.feature .icon{width:86px;height:86px;border-radius:50%;background:var(--white)}
.feature.dark .icon{background:var(--orange)}

.post{left:104px;width:654px}
.post h2{font-family:"Questrial",Arial,sans-serif;font-weight:400;font-size:25px;line-height:30px;color:#3a3a3a}
.post .sub{position:absolute;top:32px;font-size:13px;font-weight:700;color:var(--ink)}
.post .body{position:absolute;top:56px;width:478px;font-size:12.4px;line-height:19.5px;color:var(--text)}
.post .body a{color:var(--orange);font-style:italic;text-decoration:underline}
.post .photo{position:absolute;right:0;top:50px;width:142px;height:126px}
.meta{position:absolute;top:198px;left:0;display:flex;gap:0;font-size:11.5px;color:var(--muted)}
.meta span{display:flex;align-items:center;gap:6px;margin-right:40px}
.post .rule{position:absolute;left:0;width:654px;height:1px;background:var(--line);top:249px}

.comments{position:absolute;left:0;top:226px;width:654px;height:194px;background:var(--soft);border:1px solid #dadada}
.comments h3{position:absolute;left:14px;top:10px;font-size:13px;font-weight:700;color:#444}
.comment{position:absolute;left:14px;width:620px;display:flex;gap:22px}
.comment .avatar{width:34px;height:34px;border:2px solid var(--white);flex:none}
.comment p{font-size:11.5px;line-height:18px;color:var(--text)}
.comments .divider{position:absolute;left:14px;right:14px;top:98px;height:1px;background:#dcdcdc}
.comments .write{position:absolute;left:10px;top:150px;width:630px;height:30px;background:var(--white);border:1px solid #d8d8d8;font-size:11.5px;font-style:italic;color:#a0a0a0;padding:7px 10px}

.more{left:104px;top:2989px;width:654px;height:37px;background:#e6e6e6;display:flex;align-items:center;justify-content:center;gap:8px;font-size:12px;color:#444}

.side{left:793px;width:345px}
.panel-head{height:42px;background:var(--panel-head);color:var(--white);font-family:"Questrial",Arial,sans-serif;font-size:19px;display:flex;align-items:center;gap:12px;padding-left:20px}
.panel-body{border:1px solid var(--line);border-top:none}
.search{height:64px;padding:18px 18px 0}
.search div{height:34px;border:1px solid #dcdcdc;font-size:11px;color:#999;padding:9px 10px;display:flex;justify-content:space-between}

.tabs{display:flex;height:44px}
.tabs div{flex:1;background:var(--dark);color:var(--white);font-size:12px;display:flex;align-items:center;justify-content:center;gap:8px}
.tabs div:first-child{background:var(--white);color:var(--ink);border:1px solid var(--line);border-bottom:none}
.tabs i{width:14px;height:14px;border-radius:50%;border:1.5px solid currentColor;display:block}
.feed{border:1px solid var(--line);border-top:none;height:303px;position:relative}
.feed-item{position:absolute;left:10px;display:flex;gap:12px}
.feed-item .avatar{width:54px;height:58px}
.feed-item p{font-size:10.5px;line-height:15px;color:var(--text);width:140px}
.feed-item .like{margin-top:4px;width:38px;height:17px;border:1px solid #c5cde0;background:#eef1f7;font-size:9.5px;color:#4a5a8a;text-align:center;line-height:15px}

.archives li{list-style:none;height:37.5px;border-bottom:1px solid #eeeeee;margin:0 18px;font-size:12.5px;color:#555;display:flex;align-items:center;gap:14px}
.archives li::before{content:"";width:4px;height:4px;border-radius:50%;background:var(--orange)}
.archives li:last-child{border-bottom:none}

.newsletter{border:1px solid var(--line);height:168px;padding:0 16px;position:relative}
.newsletter h4{position:absolute;top:12px;left:16px;font-family:"Questrial",Arial,sans-serif;font-weight:400;font-size:19px;color:var(--ink)}
.newsletter p{position:absolute;top:46px;left:16px;font-size:11.5px}
.newsletter .field{position:absolute;top:76px;left:16px;width:308px;height:34px;border:1px solid #dcdcdc;font-size:10.5px;font-style:italic;color:#999;padding:9px 10px}
.newsletter .submit{position:absolute;top:122px;left:16px;width:92px;height:36px;background:var(--orange);color:var(--white);font-size:13px;font-weight:700;display:flex;align-items:center;justify-content:center;letter-spacing:.5px}

.footer{left:0;top:3068px;width:1200px;height:46px;background:var(--dark);color:#ddd;font-size:12px;display:flex;align-items:center;justify-content:center}
</style>
</head>
<body>

<div class="abs topbar"><div class="dots"><span></span><span></span><span></span><span></span></div></div>

<div class="abs brand">Tandem K: Or the Year I Woke Up</div>
<nav class="abs nav"><a href="#">About Me</a><a href="#">Recent Blog</a><a href="#">Reader Comments</a><a href="#">Contact Us</a></nav>

<section class="abs hero" role="img" aria-label="Silhouette of a person with arms raised against a sunset sky over mountains">
  <div class="arrow" style="left:0"><svg width="8" height="12" viewBox="0 0 8 12"><path d="M7 1 2 6l5 5" fill="none" stroke="#fff" stroke-width="2"/></svg></div>
  <div class="arrow" style="right:0"><svg width="8" height="12" viewBox="0 0 8 12"><path d="M1 1l5 5-5 5" fill="none" stroke="#fff" stroke-width="2"/></svg></div>
  <div class="tagline">A Different Kind of Company<br>A Different Kind of Tandem K</div>
</section>

<section class="abs features">
  <div class="feature"><span class="icon" role="img" aria-label="Apple icon"></span>Nutrition</div>
  <div class="feature dark"><span class="icon" role="img" aria-label="Meditation pose icon"></span>Exercise</div>
  <div class="feature"><span class="icon" role="img" aria-label="Cyclist icon"></span>Sports</div>
</section>

<!-- blog posts -->
<article class="abs post" style="top:762px">
  <h2>Lorem ipsum dolor sit</h2>
  <p class="sub">Duis aute irure dolor in reprehenderit</p>
  <p class="body">Lorem ipsum dolor sit amet, consecit adipiscing elit, sed do eiusmod tempor incididunt labore n dolorne laboris ni ut aliquip ex ena lin consequat Duis aute irure dolor in reprehenderit magna aliqua. Ut enim ad qexercitation ullamco Neque porro quisquam est, qui dolorem ipsum quia dolor sit amet, conadipi velit sed quia non numquam eius modi tempora incidunt. ipsum quia dolor sit amet, conadipi velit sed quia non numquam eius modi tempora. <a href="#">Read More</a></p>
  <div class="photo" role="img" aria-label="Photo of a man in a jacket" style="background:linear-gradient(160deg,#a48c78,#3c4a5c)"></div>
  <div class="meta">
    <span><svg width="12" height="12"><rect x="1" y="2" width="10" height="9" fill="none" stroke="#f7a11a" stroke-width="1.4"/><path d="M1 5h10" stroke="#f7a11a"/></svg>02/06/2016</span>
    <span><svg width="13" height="12"><ellipse cx="6.5" cy="5" rx="6" ry="4.5" fill="#f7a11a"/><path d="M3 8l-1 4 4-3z" fill="#f7a11a"/></svg>Leave A Comment</span>
    <span><svg width="12" height="12"><rect x="0" y="5" width="3" height="7" fill="#f7a11a"/><path d="M4 5l3-5c2 0 2 2 1.5 4H12v4l-2 4H4z" fill="#f7a11a"/></svg>Like Us</span>
    <span><svg width="12" height="12"><circle cx="10" cy="2" r="2" fill="#f7a11a"/><circle cx="2" cy="6" r="2" fill="#f7a11a"/><circle cx="10" cy="10" r="2" fill="#f7a11a"/><path d="M10 2 2 6l8 4" fill="none" stroke="#f7a11a"/></svg>Share</span>
  </div>
  <div class="comments">
    <h3>Comments</h3>
    <div class="comment" style="top:36px"><div class="avatar" role="img" aria-label="Reader avatar" style="background:#c9a48c"></div><p>Lorem ipsum dolor sit amet, consecit adipiscing elit, sed do eiusmod tempor incididunt labore n dolorne laboris ni ut aliquip ex ena lin consequat Duis aute irure dolor in reprehenderit magna aliqua. Ut enim</p></div>
    <div class="divider"></div>
    <div class="comment" style="top:108px"><div class="avatar" role="img" aria-label="Reader avatar" style="background:#b07a58"></div><p>Lorem ipsum dolor sit amet, consecit adipiscing elit, sed do eiusmod tempor incididunt labore n dolorne laboris ni ut aliquip ex ena lin consequat.</p></div>
    <div class="write">Write Comment</div>
  </div>
  <div class="rule" style="top:448px"></div>
</article>

<article class="abs post" style="top:1246px">
  <h2>Lorem ipsum dolor sit</h2>
  <p class="sub">Duis aute irure dolor in reprehenderit</p>
  <p class="body">Lorem ipsum dolor sit amet, consecit adipiscing elit, sed do eiusmod tempor incididunt labore n dolorne laboris ni ut aliquip ex ena lin consequat Duis aute irure dolor in reprehenderit magna aliqua. Ut enim ad qexercitation ullamco Neque porro quisquam est, qui dolorem ipsum quia dolor sit amet, conadipi velit sed quia non numquam eius modi tempora incidunt. ipsum quia dolor sit amet, conadipi velit sed quia non numquam eius modi tempora. <a href="#">Read More</a></p>
  <div class="photo" role="img" aria-label="Photo of a blonde woman" style="background:linear-gradient(160deg,#d8c4a8,#7a6a5c)"></div>
  <div class="meta"><span><svg width="12" height="12"><rect x="1" y="2" width="10" height="9" fill="none" stroke="#f7a11a" stroke-width="1.4"/><path d="M1 5h10" stroke="#f7a11a"/></svg>02/06/2016</span><span><svg width="13" height="12"><ellipse cx="6.5" cy="5" rx="6" ry="4.5" fill="#f7a11a"/><path d="M3 8l-1 4 4-3z" fill="#f7a11a"/></svg>Leave A Comment</span><span><svg width="12" height="12"><rect x="0" y="5" width="3" height="7" fill="#f7a11a"/><path d="M4 5l3-5c2 0 2 2 1.5 4H12v4l-2 4H4z" fill="#f7a11a"/></svg>Like Us</span><span><svg width="12" height="12"><circle cx="10" cy="2" r="2" fill="#f7a11a"/><circle cx="2" cy="6" r="2" fill="#f7a11a"/><circle cx="10" cy="10" r="2" fill="#f7a11a"/><path d="M10 2 2 6l8 4" fill="none" stroke="#f7a11a"/></svg>Share</span></div>
  <div class="rule"></div>
</article>

<article class="abs post" style="top:1542px">
  <h2>Lorem ipsum dolor sit</h2>
  <p class="sub">Duis aute irure dolor in reprehenderit</p>
  <p class="body">Lorem ipsum dolor sit amet, consecit adipiscing elit, sed do eiusmod tempor incididunt labore n dolorne laboris ni ut aliquip ex ena lin consequat Duis aute irure dolor in reprehenderit magna aliqua. Ut enim ad qexercitation ullamco Neque porro quisquam est, qui dolorem ipsum quia dolor sit amet, conadipi velit sed quia non numquam eius modi tempora incidunt. ipsum quia dolor sit amet, conadipi velit sed quia non numquam eius modi tempora. <a href="#">Read More</a></p>
  <div class="photo" role="img" aria-label="Portrait of a man in a suit" style="background:linear-gradient(160deg,#b8d0cc,#5a4a44)"></div>
  <div class="meta"><span><svg width="12" height="12"><rect x="1" y="2" width="10" height="9" fill="none" stroke="#f7a11a" stroke-width="1.4"/><path d="M1 5h10" stroke="#f7a11a"/></svg>02/06/2016</span><span><svg width="13" height="12"><ellipse cx="6.5" cy="5" rx="6" ry="4.5" fill="#f7a11a"/><path d="M3 8l-1 4 4-3z" fill="#f7a11a"/></svg>Leave A Comment</span><span><svg width="12" height="12"><rect x="0" y="5" width="3" height="7" fill="#f7a11a"/><path d="M4 5l3-5c2 0 2 2 1.5 4H12v4l-2 4H4z" fill="#f7a11a"/></svg>Like Us</span><span><svg width="12" height="12"><circle cx="10" cy="2" r="2" fill="#f7a11a"/><circle cx="2" cy="6" r="2" fill="#f7a11a"/><circle cx="10" cy="10" r="2" fill="#f7a11a"/><path d="M10 2 2 6l8 4" fill="none" stroke="#f7a11a"/></svg>Share</span></div>
  <div class="rule"></div>
</article>

<article class="abs post" style="top:1838px">
  <h2>Lorem ipsum dolor sit</h2>
  <p class="sub">Duis aute irure dolor in reprehenderit</p>
  <p class="body">Lorem ipsum dolor sit amet, consecit adipiscing elit, sed do eiusmod tempor incididunt labore n dolorne laboris ni ut aliquip ex ena lin consequat Duis aute irure dolor in reprehenderit magna aliqua. Ut enim ad qexercitation ullamco Neque porro quisquam est, qui dolorem ipsum quia dolor sit amet, conadipi velit sed quia non numquam eius modi tempora incidunt. ipsum quia dolor sit amet, conadipi velit sed quia non numquam eius modi tempora. <a href="#">Read More</a></p>
  <div class="photo" role="img" aria-label="Black and white portrait of a man in a suit" style="background:linear-gradient(160deg,#9a9a9a,#2e2e2e)"></div>
  <div class="meta"><span><svg width="12" height="12"><rect x="1" y="2" width="10" height="9" fill="none" stroke="#f7a11a" stroke-width="1.4"/><path d="M1 5h10" stroke="#f7a11a"/></svg>02/06/2016</span><span><svg width="13" height="12"><ellipse cx="6.5" cy="5" rx="6" ry="4.5" fill="#f7a11a"/><path d="M3 8l-1 4 4-3z" fill="#f7a11a"/></svg>Leave A Comment</span><span><svg width="12" height="12"><rect x="0" y="5" width="3" height="7" fill="#f7a11a"/><path d="M4 5l3-5c2 0 2 2 1.5 4H12v4l-2 4H4z" fill="#f7a11a"/></svg>Like Us</span><span><svg width="12" height="12"><circle cx="10" cy="2" r="2" fill="#f7a11a"/><circle cx="2" cy="6" r="2" fill="#f7a11a"/><circle cx="10" cy="10" r="2" fill="#f7a11a"/><path d="M10 2 2 6l8 4" fill="none" stroke="#f7a11a"/></svg>Share</span></div>
  <div class="rule"></div>
</article>

<article class="abs post" style="top:2134px">
  <h2>Lorem ipsum dolor sit</h2>
  <p class="sub">Duis aute irure dolor in reprehenderit</p>
  <p class="body">Lorem ipsum dolor sit amet, consecit adipiscing elit, sed do eiusmod tempor incididunt labore n dolorne laboris ni ut aliquip ex ena lin consequat Duis aute irure dolor in reprehenderit magna aliqua. Ut enim ad qexercitation ullamco Neque porro quisquam est, qui dolorem ipsum quia dolor sit amet, conadipi velit sed quia non numquam eius modi tempora incidunt. ipsum quia dolor sit amet, conadipi velit sed quia non numquam eius modi tempora. <a href="#">Read More</a></p>
  <div class="photo" role="img" aria-label="Photo of a businesswoman in an office" style="background:linear-gradient(160deg,#e6e2da,#8c8070)"></div>
  <div class="meta"><span><svg width="12" height="12"><rect x="1" y="2" width="10" height="9" fill="none" stroke="#f7a11a" stroke-width="1.4"/><path d="M1 5h10" stroke="#f7a11a"/></svg>02/06/2016</span><span><svg width="13" height="12"><ellipse cx="6.5" cy="5" rx="6" ry="4.5" fill="#f7a11a"/><path d="M3 8l-1 4 4-3z" fill="#f7a11a"/></svg>Leave A Comment</span><span><svg width="12" height="12"><rect x="0" y="5" width="3" height="7" fill="#f7a11a"/><path d="M4 5l3-5c2 0 2 2 1.5 4H12v4l-2 4H4z" fill="#f7a11a"/></svg>Like Us</span><span><svg width="12" height="12"><circle cx="10" cy="2" r="2" fill="#f7a11a"/><circle cx="2" cy="6" r="2" fill="#f7a11a"/><circle cx="10" cy="10" r="2" fill="#f7a11a"/><path d="M10 2 2 6l8 4" fill="none" stroke="#f7a11a"/></svg>Share</span></div>
  <div class="rule"></div>
</article>

<article class="abs post" style="top:2430px">
  <h2>Lorem ipsum dolor sit</h2>
  <p class="sub">Duis aute irure dolor in reprehenderit</p>
  <p class="body">Lorem ipsum dolor sit amet, consecit adipiscing elit, sed do eiusmod tempor incididunt labore n dolorne laboris ni ut aliquip ex ena lin consequat Duis aute irure dolor in reprehenderit magna aliqua. Ut enim ad qexercitation ullamco Neque porro quisquam est, qui dolorem ipsum quia dolor sit amet, conadipi velit sed quia non numquam eius modi tempora incidunt. ipsum quia dolor sit amet, conadipi velit sed quia non numquam eius modi tempora. <a href="#">Read More</a></p>
  <div class="photo" role="img" aria-label="Portrait of a woman in a dark blazer" style="background:linear-gradient(160deg,#f0ede8,#4a3c34)"></div>
  <div class="meta"><span><svg width="12" height="12"><rect x="1" y="2" width="10" height="9" fill="none" stroke="#f7a11a" stroke-width="1.4"/><path d="M1 5h10" stroke="#f7a11a"/></svg>02/06/2016</span><span><svg width="13" height="12"><ellipse cx="6.5" cy="5" rx="6" ry="4.5" fill="#f7a11a"/><path d="M3 8l-1 4 4-3z" fill="#f7a11a"/></svg>Leave A Comment</span><span><svg width="12" height="12"><rect x="0" y="5" width="3" height="7" fill="#f7a11a"/><path d="M4 5l3-5c2 0 2 2 1.5 4H12v4l-2 4H4z" fill="#f7a11a"/></svg>Like Us</span><span><svg width="12" height="12"><circle cx="10" cy="2" r="2" fill="#f7a11a"/><circle cx="2" cy="6" r="2" fill="#f7a11a"/><circle cx="10" cy="10" r="2" fill="#f7a11a"/><path d="M10 2 2 6l8 4" fill="none" stroke="#f7a11a"/></svg>Share</span></div>
  <div class="rule"></div>
</article>

<article class="abs post" style="top:2726px">
  <h2>Lorem ipsum dolor sit</h2>
  <p class="sub">Duis aute irure dolor in reprehenderit</p>
  <p class="body">Lorem ipsum dolor sit amet, consecit adipiscing elit, sed do eiusmod tempor incididunt labore n dolorne laboris ni ut aliquip ex ena lin consequat Duis aute irure dolor in reprehenderit magna aliqua. Ut enim ad qexercitation ullamco Neque porro quisquam est, qui dolorem ipsum quia dolor sit amet, conadipi velit sed quia non numquam eius modi tempora incidunt. ipsum quia dolor sit amet, conadipi velit sed quia non numquam eius modi tempora. <a href="#">Read More</a></p>
  <div class="photo" role="img" aria-label="Portrait of a young man in a sweater" style="background:linear-gradient(160deg,#f4f4f4,#4c3a30)"></div>
  <div class="meta"><span><svg width="12" height="12"><rect x="1" y="2" width="10" height="9" fill="none" stroke="#f7a11a" stroke-width="1.4"/><path d="M1 5h10" stroke="#f7a11a"/></svg>02/06/2016</span><span><svg width="13" height="12"><ellipse cx="6.5" cy="5" rx="6" ry="4.5" fill="#f7a11a"/><path d="M3 8l-1 4 4-3z" fill="#f7a11a"/></svg>Leave A Comment</span><span><svg width="12" height="12"><rect x="0" y="5" width="3" height="7" fill="#f7a11a"/><path d="M4 5l3-5c2 0 2 2 1.5 4H12v4l-2 4H4z" fill="#f7a11a"/></svg>Like Us</span><span><svg width="12" height="12"><circle cx="10" cy="2" r="2" fill="#f7a11a"/><circle cx="2" cy="6" r="2" fill="#f7a11a"/><circle cx="10" cy="10" r="2" fill="#f7a11a"/><path d="M10 2 2 6l8 4" fill="none" stroke="#f7a11a"/></svg>Share</span></div>
</article>

<div class="abs more"><svg width="16" height="16"><circle cx="8" cy="8" r="6.5" fill="none" stroke="#999" stroke-width="2" stroke-dasharray="3 2"/></svg>Load More Blog</div>

<!-- sidebar -->
<aside class="abs side" style="top:766px">
  <div class="panel-head"><svg width="18" height="18"><circle cx="3" cy="15" r="2.5" fill="#fff"/><path d="M1 8a9 9 0 0 1 9 9M1 2a15 15 0 0 1 15 15" fill="none" stroke="#fff" stroke-width="2.2"/></svg>Search Blog</div>
  <div class="panel-body search"><div><span>Search...</span><svg width="13" height="13"><circle cx="5.5" cy="5.5" r="4.5" fill="none" stroke="#bbb" stroke-width="1.5"/><path d="M9 9l3.5 3.5" stroke="#bbb" stroke-width="1.5"/></svg></div></div>
</aside>

<aside class="abs side" style="top:913px">
  <div class="tabs"><div><i></i>Circlebook</div><div><i></i>Chirper</div><div><i></i>Snapgram</div></div>
  <div class="feed">
    <div class="feed-item" style="top:10px"><div class="avatar" role="img" aria-label="Follower photo" style="background:#b89078"></div><div><p>Lorem Ipsum is simply dummy text of the printing and typesetting...</p><div class="like">Like</div></div></div>
    <div class="feed-item" style="top:85px"><div class="avatar" role="img" aria-label="Follower photo" style="background:#5a3a34"></div><div><p>Lorem Ipsum is simply dummy text of the printing and typesetting...</p><div class="like">Like</div></div></div>
    <div class="feed-item" style="top:160px"><div class="avatar" role="img" aria-label="Follower photo" style="background:#c8a890"></div><div><p>Lorem Ipsum is simply dummy text of the printing and typesetting...</p><div class="like">Like</div></div></div>
    <div class="feed-item" style="top:235px"><div class="avatar" role="img" aria-label="Follower photo" style="background:#4a3030"></div><div><p>Lorem Ipsum is simply dummy text of the printing and typesetting...</p><div class="like">Like</div></div></div>
  </div>
</aside>

<aside class="abs side" style="top:1293px">
  <div class="panel-head"><svg width="16" height="18"><path d="M1 1h9l5 5v11H1z" fill="none" stroke="#fff" stroke-width="1.6"/><path d="M4 9h8M4 12h8" stroke="#fff" stroke-width="1.4"/></svg>Archives</div>
  <ul class="panel-body archives" style="padding:4px 0"><li>July 2016</li><li>June 2016</li><li>May 2016</li><li>April 2016</li><li>February 2016</li></ul>
</aside>

<aside class="abs side newsletter" style="top:1567px">
  <h4>SignUp For Newsletter</h4>
  <p>Lorem ipsum dolor sit amet, consecit</p>
  <div class="field">Enter your email address</div>
  <div class="submit">SUBMIT</div>
</aside>

<div class="abs side" style="top:1771px;height:257px;background:#8e8e8e" role="img" aria-label="Advertisement poster with a quote about education"></div>
<div class="abs side" style="top:2066px;height:197px;background:linear-gradient(135deg,#c89a6a,#a87448)" role="img" aria-label="Advertisement illustration of striped legs and red sneakers, Smart. Active. Forward-Thinking."></div>

<footer class="abs footer">Copyright © 2016 &nbsp;Tandem K &nbsp;|&nbsp; All Rights Reserved.</footer>

</body>
</html>
```